Website Comps for Famous Southern BBQ Restaurant in Alabama

We need an authentic, brand-focused redesign for a restaurant.

We need an authentic look.
The client really likes this website.
https://pelmarsmokehouse.example/

I don't want to see a bunch of crazy colors.
Avoid image sliders on the homepage. I hate those.

Please mockup the following three pages:
Homepage
Interior page (for mockup purposes, you can do an About page)
Menu page

I only need the PSD's; not the website coded.

Here is the current website: www.kortiespit.example

https://pelmarsmokehouse.example/

Here are some additional stock photos. New photos will be shot, but these may help for your mock-up designs.
https://files.quillbox.example/sh/83kkqvtrd41zpa7/XQM20PbT9LyRk-wnEuvJ3tpd?dl=0
Updates

I realize we don't have a lot of high-quality photos to work with.Those will be shot.Here are some additional stock photos that may help.https://files.quillbox.example/sh/83kkqvtrd41zpa7/XQM20PbT9LyRk-wnEuvJ3tpd?dl=0 Added Saturday, June 10, 2017

Target Market(s)

United states

Industry/Entity Type

Restaurant

Number of Pages Required

3 page

Font styles to use
Sans Serif

Colors

Designer to choose colors to be used in the design.

Requirements
Must have
• An authentic look.
• The client really likes this website.
• https://pelmarsmokehouse.example/
• It's simple, bold, and vintage at the same time.
• That is what we want.
• Our existing website is
• kortiespit.example
Nice to have
• Simplicity. Something that makes the food look good.
• Possibly a background.
• Logo:
• https://files.quillbox.example/s/t62bnezwhk0qpl3/kories-pit-lakeview.png?dl=0
• Here is a sampling of photos for your comps:
• https://files.quillbox.example/sh/59ryhdupqv2ncmx/MPT4c1ZLvWeQjHoNUyrA8BfxKs?dl=0
Should not have
• Nothing too busy.
• Not too many colors.
• Keep it simple, authentic, "down home."
• No homepage image sliders.

```html
<!DOCTYPE html>
<html lang="en">
<head>
<meta charset="utf-8">
<title>Get in touch – Kortie's Pit</title>
<link href="https://fonts.googleapis.com/css2?family=Open+Sans:wght@400;600;700&family=Tangerine:wght@400;700&display=swap" rel="stylesheet">
<style>
:root{
  --ink:#1f1f1f;
  --text:#333333;
  --accent:#f0782b;
  --rule:#bdbdbd;
  --footer:#262626;
  --button:#2e2e2e;
  --brand-bg:#6b1a12;
  --brand-fg:#f4a833;
  --paper:#ffffff;
}
*{box-sizing:border-box;margin:0;padding:0}
html,body{width:1200px;height:805px;overflow:hidden;background:var(--paper)}
body{position:relative;font-family:"Open Sans",Arial,sans-serif;color:var(--text)}
.abs{position:absolute}
.section-title{left:0;width:1200px;top:42px;text-align:center;font-family:"Tangerine",cursive;font-size:56px;font-weight:400;color:var(--ink);line-height:1}
.title-ornament{left:500px;top:100px}
.col-heading{font-size:20px;font-weight:400;color:var(--ink);top:190px;line-height:1}
.contact-intro{left:160px;top:230px;width:260px;font-size:10.5px;line-height:18px}
.contact-line{left:160px;display:flex;align-items:center;gap:10px;font-size:10.5px}
.contact-line svg{width:20px;height:20px}
.hours{left:458px;top:230px;width:210px;font-size:10px;border-collapse:collapse}
.hours td{height:27.8px;vertical-align:top}
.hours .day{font-weight:700;color:var(--ink);width:118px}
.gallery{left:758px;top:237px;display:grid;grid-template-columns:repeat(3,89px);grid-auto-rows:49px;gap:4px}
.gallery div{width:89px;height:49px}
.divider{left:173px;top:465px;width:858px;height:1px;background:var(--rule)}
.brand-mark{left:574px;top:478px;width:67px;height:65px;background:var(--brand-bg);display:flex;align-items:center;justify-content:center;text-align:center;color:var(--brand-fg);font-weight:700;font-size:12px;line-height:1.1}
.about{left:280px;top:552px;width:640px;text-align:center;font-size:12.5px;line-height:19px}
.sub-heading{font-size:20px;color:var(--ink);top:623px;text-align:center;width:260px;line-height:1}
.social{left:308px;top:663px;display:flex;gap:7px}
.social span{width:29px;height:29px;border:1.6px solid var(--ink);border-radius:50%}
.newsletter{left:710px;top:664px;display:flex;height:32px}
.newsletter input{width:160px;height:32px;border:1px solid var(--ink);border-right:none;padding:0 8px;font-family:inherit;font-size:8px;color:#888}
.newsletter button{width:40px;height:32px;border:none;background:var(--button);display:flex;align-items:center;justify-content:center}
.site-footer{left:0;top:726px;width:1200px;height:79px;background:var(--footer);color:#fff;font-size:8px;font-weight:700;text-align:center;padding-top:38px}
</style>
</head>
<body>

<h1 class="abs section-title">Get in touch</h1>
<svg class="abs title-ornament" width="204" height="26" viewBox="0 0 204 26" aria-hidden="true">
  <line x1="2" y1="14" x2="80" y2="14" stroke="var(--accent)" stroke-width="1"/>
  <line x1="124" y1="14" x2="202" y2="14" stroke="var(--accent)" stroke-width="1"/>
  <g stroke="var(--accent)" stroke-width="2.4" stroke-linecap="round">
    <line x1="93" y1="5" x2="111" y2="22"/>
    <line x1="111" y1="5" x2="93" y2="22"/>
  </g>
</svg>

<h2 class="abs col-heading" style="left:162px">Contact us</h2>
<p class="abs contact-intro">Lorem ipsum dolor sit amet, consectetur adipisicing elit. Voluptatum nisi quam magni quos laborum,</p>
<div class="abs contact-line" style="top:292px">
  <svg viewBox="0 0 20 20" aria-hidden="true"><path d="M2 7c0-3 16-3 16 0v2h-4V7H6v2H2z M5 10h10l2 7H3z" fill="var(--ink)"/><circle cx="10" cy="13.5" r="2" fill="#fff"/></svg>
  <span>+ 1234567890</span>
</div>
<div class="abs contact-line" style="top:329px">
  <svg viewBox="0 0 20 20" aria-hidden="true"><path d="M2 6h16v10H2z" fill="var(--ink)"/><path d="M2 6l8 6 8-6" fill="none" stroke="#fff" stroke-width="1.3"/></svg>
  <span>hello@kortiespit.example</span>
</div>
<div class="abs contact-line" style="top:367px">
  <svg viewBox="0 0 20 20" aria-hidden="true"><path d="M10 2L1 10h3v8h4v-5h4v5h4v-8h3z" fill="var(--ink)"/></svg>
  <span>1234, Lorem ipsum,1234567890</span>
</div>

<h2 class="abs col-heading" style="left:455px">Opening hour</h2>
<table class="abs hours">
  <tr><td class="day">Lorem</td><td>11AM to 11PM</td></tr>
  <tr><td class="day">Lorem</td><td>11AM to 11PM</td></tr>
  <tr><td class="day">Lorem</td><td>11AM to 11PM</td></tr>
  <tr><td class="day">Lorem</td><td>11AM to 11PM</td></tr>
  <tr><td class="day">Lorem</td><td>11AM to 11PM</td></tr>
  <tr><td class="day">Lorem</td><td>11AM to 11PM</td></tr>
  <tr><td class="day">Lorem</td><td>11AM to 11PM</td></tr>
</table>

<h2 class="abs col-heading" style="left:757px">Photo wall</h2>
<div class="abs gallery">
  <div role="img" aria-label="Fresh vegetables and grapes" style="background:linear-gradient(135deg,#d8692a,#8fae3a,#5a3a4a)"></div>
  <div role="img" aria-label="Pizza slices" style="background:linear-gradient(135deg,#e2a040,#c2401f)"></div>
  <div role="img" aria-label="Grilled skewers" style="background:linear-gradient(135deg,#2a1c18,#b8401f,#3a2a20)"></div>
  <div role="img" aria-label="Tacos with tomato" style="background:linear-gradient(135deg,#c9542a,#7a2a18)"></div>
  <div role="img" aria-label="Bananas, apples and green beans" style="background:linear-gradient(135deg,#e7d23e,#7fb43a,#3e7a2a)"></div>
  <div role="img" aria-label="Bowls of chili" style="background:linear-gradient(135deg,#e8ddd0,#b8642e)"></div>
  <div role="img" aria-label="Burger and fries" style="background:linear-gradient(135deg,#f0d070,#9a5a2a,#e8e0c8)"></div>
  <div role="img" aria-label="Barbecue meat skewers" style="background:linear-gradient(135deg,#5a1a10,#b8361a,#3a3a1a)"></div>
  <div role="img" aria-label="Burger, fries and drink" style="background:linear-gradient(135deg,#f2c23a,#d83a22,#f4f0e8)"></div>
</div>

<div class="abs divider"></div>
<div class="abs brand-mark">Kortie's<br>Pit</div>
<p class="abs about">Lorem ipsum dolor sit amet, consectetur adipisicing elit. Voluptatum nisi quam magni quos laborum, dolorum accusamus maiores, iste aspernatur reprehenderit omnis. Odio consectetur itaque</p>

<h2 class="abs sub-heading" style="left:249px">Follow us on</h2>
<div class="abs social" aria-label="Social links">
  <span></span><span></span><span></span><span></span>
</div>

<h2 class="abs sub-heading" style="left:676px">Newsletter</h2>
<form class="abs newsletter">
  <input type="email" placeholder="Enter your email adress">
  <button type="button" aria-label="Subscribe">
    <svg width="16" height="11" viewBox="0 0 16 11"><rect x="0.5" y="0.5" width="15" height="10" fill="none" stroke="var(--accent)"/><path d="M0.5 0.5l7.5 6 7.5-6" fill="none" stroke="var(--accent)"/></svg>
  </button>
</form>

<footer class="abs site-footer">Copyright 2015 Kortie's Pit, LLC</footer>

</body>
</html>
```